Road Construction Company needs business cards

We would like a new business card designed for our business.

We're a road construction company based in Qld, Australia.

Can the business card please have the following information on it.

Name: Warren Halbeck
Position: General Manager
Phone: 0472 915 348
Email: Warren.halbeck@tovrin.com.au
Address: 87 Marrow Ave, Pendlebay, QLD, 4023
Website: www.tovrin.com.au

Visually we'd like the card to be professional and simple.

Attached is our logo.

Our website is www.tovrin.com.au

Target Market(s)

Men aged 25-60

Contact Information for Business Card

As listed in project description

Font styles to use
Serif

Requirements
Must have
• Large logo on back of card

```html
<!DOCTYPE html>
<html lang="en">
<head>
<meta charset="utf-8">
<title>Tovrin Road Construction – Business Card</title>
<link rel="stylesheet" href="https://fonts.googleapis.com/css2?family=Open+Sans:wght@400;600;800&display=swap">
<style>
  :root {
    --backdrop: #e9e7e3;
    --card-black: #202024;
    --brand-blue: #1b5bb0;
    --accent-blue: #3fa3dc;
    --text-white: #f2f2f2;
    --plate-blue-light: #1f63ba;
    --plate-blue-dark: #174f9e;
  }
  * { box-sizing: border-box; margin: 0; padding: 0; }
  html, body { width: 1200px; height: 780px; overflow: hidden; }
  body {
    background: var(--backdrop);
    font-family: "Open Sans", Arial, sans-serif;
    position: relative;
  }
  .card {
    position: absolute;
    top: 235px;
    width: 540px;
    height: 310px;
    border-radius: 18px;
    overflow: hidden;
    box-shadow: 0 10px 26px rgba(0,0,0,.25);
  }
  /* Front */
  .card-front { left: 40px; background: var(--card-black); color: var(--text-white); }
  .wordmark { position: absolute; left: 30px; top: 22px; color: var(--brand-blue); font-weight: 800; line-height: 1; }
  .wordmark-name { display: block; font-size: 46px; letter-spacing: 1px; }
  .wordmark-tag { display: block; font-size: 10.5px; letter-spacing: 5.4px; margin-top: 4px; }
  .contact-list { position: absolute; left: 30px; top: 122px; list-style: none; font-size: 12.5px; line-height: 1.45; }
  .contact-list li { display: flex; align-items: flex-start; gap: 7px; }
  .contact-list .address { padding-left: 19px; margin-bottom: 2px; }
  .contact-icon { width: 12px; height: 12px; margin-top: 3px; flex: none; fill: var(--accent-blue); }
  .person { position: absolute; right: 48px; top: 150px; text-align: right; }
  .person-name { color: var(--accent-blue); font-weight: 600; font-size: 24px; line-height: 1.15; }
  .person-role { font-size: 14px; }
  .edge-tab { position: absolute; right: 0; top: 170px; width: 16px; height: 34px; background: var(--accent-blue); }
  /* Back */
  .card-back { left: 620px; }
  .plate-texture {
    position: absolute; inset: 0;
    background: linear-gradient(135deg, var(--plate-blue-light), var(--plate-blue-dark));
  }
  .wordmark-large { position: absolute; left: 0; right: 0; top: 96px; text-align: center; color: #ffffff; font-weight: 800; line-height: 1; }
  .wordmark-large .wordmark-name { font-size: 92px; letter-spacing: 3px; }
  .wordmark-large .wordmark-tag { font-size: 17px; letter-spacing: 9px; margin-top: 8px; }
</style>
</head>
<body>
  <section class="card card-front" aria-label="Card front">
    <div class="wordmark">
      <span class="wordmark-name">TOVRIN</span>
      <span class="wordmark-tag">ROAD CONSTRUCTION</span>
    </div>
    <ul class="contact-list">
      <li class="address">87 Marrow Ave,<br>Pendlebay, QLD, 4023</li>
      <li>
        <svg class="contact-icon" viewBox="0 0 24 24" aria-hidden="true"><path d="M6.6 10.8a15 15 0 0 0 6.6 6.6l2.2-2.2c.3-.3.7-.4 1-.2 1.1.4 2.3.6 3.6.6.6 0 1 .4 1 1V20c0 .6-.4 1-1 1A17 17 0 0 1 3 4c0-.6.4-1 1-1h3.5c.6 0 1 .4 1 1 0 1.3.2 2.5.6 3.6.1.3 0 .7-.2 1z"/></svg>
        <span>0472 915 348</span>
      </li>
      <li>
        <svg class="contact-icon" viewBox="0 0 24 24" aria-hidden="true"><path d="M2 5h20v14H2z M4 7v.5l8 5 8-5V7l-8 5z" fill-rule="evenodd"/></svg>
        <span>www.tovrin.com.au</span>
      </li>
      <li>
        <svg class="contact-icon" viewBox="0 0 24 24" aria-hidden="true"><circle cx="12" cy="12" r="10"/></svg>
        <span>Warren.halbeck@tovrin.com.au</span>
      </li>
    </ul>
    <div class="person">
      <p class="person-name">Warren Halbeck</p>
      <p class="person-role">General Manager</p>
    </div>
    <div class="edge-tab"></div>
  </section>

  <section class="card card-back" aria-label="Card back">
    <div class="plate-texture" role="img" aria-label="Blue diamond-plate chevron pattern background"></div>
    <div class="wordmark-large">
      <span class="wordmark-name">TOVRIN</span>
      <span class="wordmark-tag">ROAD CONSTRUCTION</span>
    </div>
  </section>
</body>
</html>
```